Business Card Design for a Software Startup

We'd like to have a business card design. We already have a logo. Basically what we need is a clean design with name, address, cellphone and phone numbers, e-mail and web site address (front) and a space on the back with our logo with the company name on the right side and some texts on the bottom.
We are a development and consulting company in Brazil with highly qualified team of professionals in Java, iOS and Android development and consulting.

Target Market(s)

CIO, IT managers of mid to big size companies

Industry/Entity Type

Business

```html
<!DOCTYPE html>
<html lang="en">
<head>
<meta charset="utf-8">
<title>Vextra Business Card</title>
<link rel="stylesheet" href="https://fonts.googleapis.com/css2?family=Open+Sans:wght@400;600;700&display=swap">
<style>
  :root {
    --page-bg: #eceef1;
    --card-bg: #ffffff;
    --navy: #1b3a78;
    --navy-deep: #15306b;
    --blue: #1f6fc0;
    --sky: #2aa3e0;
    --text-on-blue: #ffffff;
    --web-text: #333333;
  }
  * { box-sizing: border-box; margin: 0; padding: 0; }
  html, body { width: 1200px; height: 720px; overflow: hidden; }
  body {
    background: var(--page-bg);
    font-family: "Open Sans", Arial, sans-serif;
    position: relative;
  }
  .card {
    position: absolute;
    top: 206px;
    width: 540px;
    height: 308px;
    background: var(--card-bg);
    box-shadow: 0 6px 18px rgba(0,0,0,0.12);
    overflow: hidden;
  }
  .card-front { left: 45px; }
  .card-back { left: 615px; }

  .front-arc { position: absolute; inset: 0; }

  .brand { position: absolute; display: flex; align-items: center; gap: 12px; }
  .brand-square {
    width: 34px; height: 34px; border-radius: 4px;
    background: var(--blue);
  }
  .brand-name {
    font-weight: 700; color: var(--navy-deep);
    letter-spacing: 1px; line-height: 1;
  }
  .card-front .brand { left: 34px; top: 188px; }
  .card-front .brand-name { font-size: 40px; }

  .contact {
    position: absolute; right: 26px; top: 18px;
    color: var(--text-on-blue); text-align: right;
  }
  .contact-name { font-size: 19px; font-weight: 700; line-height: 1.1; }
  .contact-title { font-size: 12px; margin-bottom: 12px; }
  .contact-list { list-style: none; font-size: 12.5px; line-height: 1.45; }
  .contact-list li { display: flex; justify-content: flex-end; align-items: center; gap: 5px; }
  .contact-list svg { width: 11px; height: 11px; flex: none; }
  .contact-address { margin-top: 6px; font-size: 12.5px; line-height: 1.45; }

  .card-back .brand {
    left: 50%; top: 112px; transform: translateX(-50%);
  }
  .card-back .brand-square { width: 40px; height: 40px; }
  .card-back .brand-name { font-size: 48px; }
  .back-web {
    position: absolute; left: 0; right: 0; top: 212px;
    text-align: center; font-size: 17px; letter-spacing: 4px;
    color: var(--web-text);
  }
</style>
</head>
<body>

<section class="card card-front" aria-label="Business card front">
  <svg class="front-arc" viewBox="0 0 540 308" aria-hidden="true">
    <defs>
      <linearGradient id="arcFill" x1="0" y1="0" x2="1" y2="0">
        <stop offset="0" stop-color="#2aa3e0"/>
        <stop offset="0.55" stop-color="#1f6fc0"/>
        <stop offset="1" stop-color="#1b3a78"/>
      </linearGradient>
    </defs>
    <circle cx="620" cy="-20" r="334" fill="var(--navy)"/>
    <circle cx="620" cy="-20" r="318" fill="#ffffff"/>
    <circle cx="620" cy="-20" r="308" fill="url(#arcFill)"/>
  </svg>

  <div class="brand">
    <span class="brand-square"></span>
    <span class="brand-name">VEXTRA</span>
  </div>

  <div class="contact">
    <p class="contact-name">Your Name</p>
    <p class="contact-title">Title</p>
    <ul class="contact-list">
      <li>
        <svg viewBox="0 0 12 12"><circle cx="6" cy="6" r="5.2" fill="none" stroke="#fff" stroke-width="1.2"/><path d="M4 3.5l1 1-0.6 0.8a4 4 0 0 0 2.3 2.3l0.8-0.6 1 1-0.8 0.8C5.5 8.6 3.4 6.5 3.2 4.3z" fill="#fff"/></svg>
        123-456-7890
      </li>
      <li>
        <svg viewBox="0 0 12 12"><rect x="3" y="1" width="6" height="10" rx="1.2" fill="#fff"/><rect x="4" y="2.3" width="4" height="6" fill="#1f6fc0"/></svg>
        456-085-4321
      </li>
      <li>
        <svg viewBox="0 0 12 12"><rect x="1" y="3" width="10" height="7" rx="1" fill="#fff"/><path d="M1.5 3.5L6 7l4.5-3.5" fill="none" stroke="#1f6fc0" stroke-width="1"/></svg>
        yourname@vextra.com
      </li>
      <li>
        <svg viewBox="0 0 12 12"><circle cx="6" cy="6" r="5" fill="none" stroke="#fff" stroke-width="1.1"/><ellipse cx="6" cy="6" rx="2.2" ry="5" fill="none" stroke="#fff" stroke-width="1"/><path d="M1 6h10" stroke="#fff" stroke-width="1"/></svg>
        www.vextra.com
      </li>
    </ul>
    <p class="contact-address">Door No. Street Name<br>City Name<br>State, Zip Codeo</p>
  </div>
</section>

<section class="card card-back" aria-label="Business card back">
  <div class="brand">
    <span class="brand-square"></span>
    <span class="brand-name">VEXTRA</span>
  </div>
  <p class="back-web">www.vextra.com</p>
</section>

</body>
</html>
```